Website design with eCommerce for revolutionary new product in the manufacturing industry.

We need a website designed for a precision manufacturing company based in the suburbs of Minneapolis, Minnesota called Velkrin Manufacturing. We have a revolutionary new product, the TARN LOCK, to introduce and sell through an eCommerce storefront. The website would include company information, product information, and the storefront. Green is a color that represents Velkrin Manufacturing. The final design should communicate that we exclusively offer premium products at a premium price. The design should also let the customer know they are the focus of our work.

Target Market(s)

Machinists and machine shops

Industry/Entity Type

Manufacturing and machine shops

Coding

Coded - Design and coding required

Font styles to use
Sans Serif

Colors
59FF00
82FF00
B8FF75
E3FFCB
F4FFEA

Requirements
Must have
• eCommerce storefront, Made in USA references
Nice to have
• Home page, TARN LOCK Product page, About Us, Capabilities, Contact, etc.
Should not have
• Should not be too much text and reading.

```html
<!DOCTYPE html>
<html lang="en">
<head>
<meta charset="utf-8">
<title>Gallery – TARN LOCK</title>
<link href="https://fonts.googleapis.com/css2?family=Audiowide&family=Poppins:wght@400;500;600&display=swap" rel="stylesheet">
<style>
:root{
  --green:#59ff00;
  --bg:#121212;
  --nav:#1a1a1a;
  --footer:#0a0a0a;
  --field:#262626;
  --text:#ffffff;
  --muted:#d6d6d6;
}
*{box-sizing:border-box;margin:0;padding:0}
html,body{width:723px;height:1200px;overflow:hidden;background:var(--bg);font-family:"Poppins",sans-serif;color:var(--text)}
.page{position:relative;width:723px;height:1200px}
.abs{position:absolute}
.topbar{left:0;top:0;width:723px;height:46px;background:var(--nav);z-index:3}
.brand{font-family:"Poppins",sans-serif;font-weight:600;color:#fff;letter-spacing:.5px}
.topbar .brand{position:absolute;left:54px;top:14px;font-size:14px}
.nav{position:absolute;left:186px;top:19px;display:flex;gap:10px;font-size:6.6px;font-weight:500;white-space:nowrap}
.nav .active{color:var(--green)}
.nav-contact{position:absolute;right:0;top:0;width:63px;height:46px;background:var(--green);color:#111;font-size:7.4px;font-weight:600;display:flex;align-items:center;justify-content:center}
.hero-photo{left:0;top:46px;width:723px;height:234px;background:radial-gradient(circle at 50% 50%,#9a9a9a,#4a4a4a 60%,#2d2a26)}
.hero-shape{left:0;top:150px;z-index:1}
.hero-title{left:0;top:118px;width:723px;text-align:center;font-family:"Audiowide",sans-serif;font-size:33px;letter-spacing:1px;z-index:2}
.section-title{left:0;top:308px;width:723px;text-align:center;font-family:"Audiowide",sans-serif;font-size:21px;letter-spacing:.5px}
.section-rule{left:336px;top:340px;width:51px;height:2px;background:var(--green)}
.section-sub{left:0;top:356px;width:723px;text-align:center;font-size:8.6px;color:var(--muted)}
.shot{border-radius:7px}
.s1{left:53px;top:396px;width:119px;height:165px;background:linear-gradient(135deg,#d9d4c6,#9c8a63 50%,#c9c2b0)}
.s2{left:177px;top:396px;width:119px;height:165px;background:linear-gradient(135deg,#8a8a8a,#2a2a2a 50%,#b8b8b8)}
.s3{left:302px;top:396px;width:119px;height:165px;background:radial-gradient(circle,#a8a8a8,#4c4c4c 70%,#5a4a34)}
.s4{left:425px;top:396px;width:243px;height:165px;background:radial-gradient(ellipse at 55% 40%,#d2d2d2,#6a6a6a 55%,#3a3a3a)}
.s5{left:53px;top:567px;width:244px;height:165px;background:radial-gradient(circle,#bdbdbd,#6b6b6b 60%,#3e3e3e)}
.s6{left:302px;top:567px;width:118px;height:165px;background:radial-gradient(circle,#d4d0c8,#8d8a85 60%,#5c5a57)}
.s7{left:425px;top:567px;width:120px;height:165px;background:linear-gradient(160deg,#1d5bb0,#b99a5a 50%,#1c4f9c)}
.s8{left:550px;top:567px;width:118px;height:165px;background:radial-gradient(circle,#8fa2b8,#1d2d66 60%,#0e1738)}
.load-more{left:328px;top:781px;width:67px;height:24px;border-radius:3px;background:#2e2e2e;font-size:7.2px;font-weight:600;display:flex;align-items:center;justify-content:center}
.footer-shape{left:0;top:820px}
.footer .brand{position:absolute;left:0;top:924px;width:723px;text-align:center;font-size:21px}
.col-title{font-family:"Audiowide",sans-serif;font-size:9.6px;top:988px}
.links{left:87px;top:1013px;list-style:none;font-size:7px;line-height:13.4px;color:var(--muted)}
.social{left:229px;top:1016px;list-style:none;font-size:7.2px;color:var(--muted)}
.social li{display:flex;align-items:center;gap:5px;height:21.4px}
.social .ico{width:15px;height:15px;background:#262626;border-radius:2px;display:inline-block}
.email{left:354px;top:1017px;font-size:7.6px;color:var(--muted);line-height:12px;display:flex;gap:5px}
.field{left:483px;width:156px;height:21px;background:var(--field);border-radius:2px;font-size:7px;color:#cfcfcf;padding-left:9px;display:flex;align-items:center}
.submit{left:483px;top:1096px;width:55px;height:21px;background:#fff;color:#111;border-radius:2px;font-size:7.4px;font-weight:600;display:flex;align-items:center;justify-content:center}
.divider{left:53px;top:1161px;width:615px;height:1px;background:#2a2a2a}
.copyright{left:0;top:1176px;width:723px;text-align:center;font-size:7.6px;font-weight:600}
.to-top{left:681px;top:1150px;width:28px;height:27px;background:var(--green);display:flex;align-items:center;justify-content:center}
</style>
</head>
<body>
<div class="page">
  <header class="topbar abs">
    <span class="brand">TARN LOCK</span>
    <nav class="nav">
      <span>WHY VELKRIN MANUFACTURING?</span>
      <span>WHAT WE DO</span>
      <span>HOW WE MAKE IT BETTER</span>
      <span>CAPABILITIES</span>
      <span class="active">GALLERY</span>
      <span>ABOUT US</span>
      <span>WISDOM</span>
    </nav>
    <div class="nav-contact">CONTACT</div>
  </header>

  <div class="hero-photo abs" role="img" aria-label="Rows of machined metal parts on a wooden surface"></div>
  <svg class="hero-shape abs" width="723" height="131" viewBox="0 0 723 131">
    <polygon points="0,130 723,49 723,131 0,131" fill="#121212"/>
    <polygon points="16,129 723,19 723,49" fill="#59ff00"/>
  </svg>
  <h1 class="hero-title abs">GALLERY</h1>

  <h2 class="section-title abs">OUR PROJECTS</h2>
  <div class="section-rule abs"></div>
  <p class="section-sub abs">Here are some of the projects we've created over the years.</p>

  <div class="shot s1 abs" role="img" aria-label="Machined aluminium rings on wood"></div>
  <div class="shot s2 abs" role="img" aria-label="Close-up of a machined part"></div>
  <div class="shot s3 abs" role="img" aria-label="Rows of machined metal pieces"></div>
  <div class="shot s4 abs" role="img" aria-label="Grid of cylindrical machined pins"></div>
  <div class="shot s5 abs" role="img" aria-label="Metal shavings"></div>
  <div class="shot s6 abs" role="img" aria-label="Perforated metal disc"></div>
  <div class="shot s7 abs" role="img" aria-label="Brass blocks on blue surface"></div>
  <div class="shot s8 abs" role="img" aria-label="Blue metal coils"></div>

  <div class="load-more abs">LOAD MORE</div>

  <footer class="footer">
    <svg class="footer-shape abs" width="723" height="380" viewBox="0 0 723 380">
      <polygon points="0,112 723,0 723,380 0,380" fill="#0a0a0a"/>
    </svg>
    <span class="brand">TARN LOCK</span>

    <h3 class="col-title abs" style="left:87px">HELPFUL LINKS</h3>
    <h3 class="col-title abs" style="left:232px">INFORMATION</h3>
    <h3 class="col-title abs" style="left:354px">CONTACT US</h3>
    <h3 class="col-title abs" style="left:482px">GET IN TOUCH</h3>

    <ul class="links abs">
      <li>Why Velkrin manufacturing?</li>
      <li>What We Do</li>
      <li>How We Make It Better</li>
      <li>Capabilities</li>
      <li>Gallery</li>
      <li>About Us</li>
      <li>Wisdom</li>
      <li>Contact Us</li>
    </ul>

    <ul class="social abs">
      <li><span class="ico"></span>Friendpage</li>
      <li><span class="ico"></span>Chirper</li>
      <li><span class="ico"></span>Searchly</li>
      <li><span class="ico"></span>Linkwork</li>
      <li><span class="ico"></span>Vidstream</li>
    </ul>

    <div class="email abs">
      <svg width="9" height="7" viewBox="0 0 9 7"><rect width="9" height="7" rx="1" fill="#59ff00"/><path d="M0.5 0.8 L4.5 4 L8.5 0.8" stroke="#0a0a0a" stroke-width="1" fill="none"/></svg>
      <span>Email:<br>info@tarnlock-mfg.com</span>
    </div>

    <div class="field abs" style="top:1017px">Enter Name</div>
    <div class="field abs" style="top:1041px">Enter Company</div>
    <div class="field abs" style="top:1065px">Enter Country</div>
    <div class="submit abs">SUBMIT</div>

    <div class="divider abs"></div>
    <p class="copyright abs">© COPYRIGHT 2022 TARN LOCK, ALL RIGHTS RESERVED</p>
    <div class="to-top abs">
      <svg width="8" height="10" viewBox="0 0 8 10"><path d="M4 10 V1 M1 4 L4 1 L7 4" stroke="#111" stroke-width="1" fill="none"/></svg>
    </div>
  </footer>
</div>
</body>
</html>
```